Modern Business Card for Larkwell 2018

Our company assumes the best about people. We are creating an online community of entrepreneurs and business leaders who struggle with marketing their business online.

This business card should POP! We recently got a new logo and are launching a new website next month, so our business cards should make a statement that feels:
-Fresh
-Smart
-Trustworthy
-Fun

Target Market(s)

small business owners, entrepreneurs

Industry/Entity Type

Digital Marketing

Contact Information for Business Card

Dimensions: 3.5" x 2"

Font styles to use
Sans Serif

Colors
f37122
ffffff

Requirements
Must have
• We need a business card with a modern, bold design. We will use one side of the card as a lead-generation offer, so text on one side will need to fit up to 140 characters. The business card should stick to our core colors (orange, black, and white).
Nice to have
• We think a vertical "portrait" design could be interesting.
Should not have
• Should not look like a traditional business card. The round icon should stand out from a distance.

```html
<!DOCTYPE html>
<html lang="en">
<head>
<meta charset="utf-8">
<title>Larkwell Business Card</title>
<link href="https://fonts.googleapis.com/css2?family=Open+Sans:wght@400;600;700;800&display=swap" rel="stylesheet">
<style>
  :root {
    --orange: #f37122;
    --orange-deep: #d95f14;
    --black: #1e1e1e;
    --white: #ffffff;
    --paper: #f4f4f4;
    --grey: #555555;
    --backdrop: #e6e4e1;
    --note: #ececec;
  }
  * { box-sizing: border-box; margin: 0; padding: 0; }
  html, body { width: 1200px; height: 960px; overflow: hidden; }
  body {
    background: var(--backdrop);
    font-family: "Open Sans", Arial, sans-serif;
    position: relative;
  }
  .card {
    position: absolute;
    left: 250px;
    width: 700px;
    height: 400px;
    overflow: hidden;
    box-shadow: 0 6px 18px rgba(0,0,0,0.18);
  }

  /* Back: lead-generation side */
  .card-back { top: 50px; background: var(--orange); color: var(--white); }
  .back-mark {
    position: absolute; left: 70px; top: 70px;
    width: 170px; height: 170px; border-radius: 50%;
    background: var(--white);
  }
  .back-divider {
    position: absolute; left: 300px; top: 40px;
    width: 2px; height: 220px; background: rgba(255,255,255,0.35);
  }
  .offer { position: absolute; left: 335px; top: 42px; width: 330px; }
  .offer-headline {
    font-weight: 800; font-size: 25px; line-height: 1.08;
    text-transform: uppercase; letter-spacing: 0.2px;
  }
  .offer-body { margin-top: 10px; font-size: 17px; line-height: 1.3; font-weight: 400; }
  .offer-url { margin-top: 10px; font-size: 20px; font-weight: 700; }
  .note-field {
    position: absolute; left: 40px; right: 40px; bottom: 36px; height: 100px;
    background: var(--note); border-radius: 16px;
    padding: 30px 30px 0;
  }
  .note-line { height: 1px; background: var(--grey); margin-bottom: 30px; }

  /* Front: contact side */
  .card-front { top: 500px; background: var(--paper); }
  .front-bands { position: absolute; inset: 0; }
  .brand { position: absolute; left: 60px; top: 125px; width: 290px; text-align: center; }
  .brand-dot {
    width: 34px; height: 34px; border-radius: 50%;
    background: var(--orange); margin: 0 auto 8px;
  }
  .brand-name {
    font-weight: 800; font-size: 50px; letter-spacing: 2px;
    color: var(--black); line-height: 1;
  }
  .brand-tagline {
    margin-top: 8px; font-weight: 700; font-size: 13px;
    letter-spacing: 1.6px; text-transform: uppercase; color: var(--black);
  }
  .front-divider {
    position: absolute; left: 380px; top: 120px;
    width: 2px; height: 140px; background: #c9c9c9;
  }
  .contact { position: absolute; left: 410px; top: 170px; }
  .contact-name {
    font-weight: 800; font-size: 24px; color: var(--orange);
    text-transform: uppercase; line-height: 1.1;
  }
  .contact-role {
    font-weight: 800; font-size: 19px; color: var(--black);
    text-transform: uppercase; line-height: 1.25;
  }
  .contact-email { font-size: 17px; color: var(--grey); line-height: 1.3; }
</style>
</head>
<body>

<section class="card card-back" aria-label="Card back">
  <div class="back-mark" aria-hidden="true"></div>
  <div class="back-divider"></div>
  <div class="offer">
    <p class="offer-headline">Reach more people.<br>Make more money.<br>Create more impact.</p>
    <p class="offer-body">Get your free Larkwell Starter Package and our marketing guide today at</p>
    <p class="offer-url">Larkwellnow.com/start</p>
  </div>
  <div class="note-field">
    <div class="note-line"></div>
    <div class="note-line"></div>
  </div>
</section>

<section class="card card-front" aria-label="Card front">
  <svg class="front-bands" width="700" height="400" viewBox="0 0 700 400" aria-hidden="true">
    <polygon points="0,0 700,0 700,42 0,10" fill="var(--black)"/>
    <polygon points="0,330 700,318 700,400 0,400" fill="var(--orange)"/>
  </svg>
  <div class="brand">
    <div class="brand-dot"></div>
    <div class="brand-name">LARKWELL</div>
    <div class="brand-tagline">Tell stories that inspire action</div>
  </div>
  <div class="front-divider"></div>
  <div class="contact">
    <p class="contact-name">Dana Whitfield</p>
    <p class="contact-role">Story Marketing Coach</p>
    <p class="contact-email">dana@larkwellnow.com</p>
  </div>
</section>

</body>
</html>
```